Request for Business Card Design

Hi. My name is Marlene, I am looking for a new business card design for my company, Quarrow Signal Instruments, LLC. I really like the design you did for Tarsel Venture and was hoping you could do something similar using our full logo and our mark. I am also open to any raised texture design using our mark. I have attached our full logo, which would need to be somewhere on the card, as well as the mark in both outline and full form, as well as our brand colors / guide. The card does not have to be white, as long as our logo and mark appear. I actually like darker colored business cards more, but am open to all options. If you are interested in working with me, please let me know. We would also take the business card design into letterhead design if you can do that.

```html
<!DOCTYPE html>
<html lang="en">
<head>
<meta charset="utf-8">
<title>Quarrow Signal Instruments – Business Card</title>
<link href="https://fonts.googleapis.com/css2?family=Open+Sans:wght@400;600;800&display=swap" rel="stylesheet">
<style>
  :root {
    --stage: #232323;
    --card-dark: #3e3e41;
    --brand-blue: #1597c2;
    --brand-blue-light: #4fb4d6;
    --brand-blue-deep: #0f86ae;
    --ink-white: #ffffff;
    --ink-grey: #3a3a3d;
  }
  * { margin: 0; padding: 0; box-sizing: border-box; }
  html, body { width: 1200px; height: 780px; overflow: hidden; }
  body {
    background: var(--stage);
    font-family: "Open Sans", Arial, sans-serif;
    position: relative;
  }
  .card {
    position: absolute;
    width: 560px;
    height: 320px;
    border-radius: 22px;
    overflow: hidden;
    box-shadow: 0 14px 30px rgba(0,0,0,.55);
  }

  /* Back of card */
  .card-back { left: 60px; top: 60px; border: 3px solid var(--brand-blue-deep); }
  .card-back .pattern-field {
    position: absolute; inset: 0;
    background: linear-gradient(215deg, var(--brand-blue-light) 0%, var(--brand-blue) 45%, var(--brand-blue-deep) 100%);
  }
  .card-back .corner-brand {
    position: absolute; right: 36px; bottom: 34px;
    display: flex; align-items: center; gap: 8px;
    color: var(--ink-grey);
  }
  .corner-brand .brand-dot {
    width: 20px; height: 20px; border-radius: 50%; background: var(--ink-white);
  }
  .corner-brand .brand-name { font-weight: 800; font-size: 16px; letter-spacing: 2px; line-height: 1; }

  /* Front of card */
  .card-front { left: 580px; top: 400px; background: var(--card-dark); border: 3px solid var(--brand-blue); }
  .card-front .bands { position: absolute; inset: 0; }
  .front-brand {
    position: absolute; left: 24px; top: 26px;
    display: flex; align-items: center; gap: 14px;
    color: var(--ink-white);
  }
  .front-brand .brand-dot {
    width: 46px; height: 46px; border-radius: 50%; background: var(--brand-blue);
  }
  .front-brand .brand-name { font-weight: 800; font-size: 36px; letter-spacing: 4px; line-height: 1; }
  .front-brand .brand-tagline { font-weight: 600; font-size: 10.5px; letter-spacing: 1.2px; margin-top: 3px; }

  .holder {
    position: absolute; right: 28px; top: 142px; text-align: right;
  }
  .holder-name { color: var(--brand-blue); font-weight: 800; font-size: 38px; line-height: 1; }
  .holder-role { color: var(--ink-white); font-weight: 600; font-size: 15px; margin-top: 2px; }

  .address {
    position: absolute; left: 96px; top: 120px;
    color: var(--ink-white); font-size: 14px; line-height: 1.35;
  }
  .contacts {
    position: absolute; left: 78px; top: 172px;
    list-style: none; color: var(--ink-white); font-size: 13.5px; line-height: 1.3;
  }
  .contacts li { display: flex; align-items: center; gap: 8px; }
  .contacts svg { width: 12px; height: 12px; fill: var(--brand-blue); flex: none; }
</style>
</head>
<body>

  <section class="card card-back" aria-label="Business card back">
    <div class="pattern-field" role="img" aria-label="Repeating brand mark pattern fading across a blue field"></div>
    <div class="corner-brand">
      <span class="brand-dot"></span>
      <span class="brand-name">QUARROW</span>
    </div>
  </section>

  <section class="card card-front" aria-label="Business card front">
    <svg class="bands" viewBox="0 0 554 314" preserveAspectRatio="none" aria-hidden="true">
      <polygon points="330,244 554,244 554,256 345,256" fill="var(--ink-white)"/>
      <polygon points="0,262 325,262 345,256 554,256 554,264 352,264 336,280 0,280" fill="var(--brand-blue)"/>
    </svg>

    <div class="front-brand">
      <span class="brand-dot"></span>
      <div>
        <div class="brand-name">QUARROW</div>
        <div class="brand-tagline">SIGNAL INSTRUMENTS</div>
      </div>
    </div>

    <div class="address">
      1180 Harbor Ridge Road<br>
      Belmont Falls, CO 80210
    </div>

    <ul class="contacts">
      <li>
        <svg viewBox="0 0 12 12"><path d="M2.5 0.8l2 2-1 1.4c.7 1.5 1.8 2.6 3.3 3.3l1.4-1 2 2-1.4 1.8C5.4 10.1 1.9 6.6 0.7 2.2z"/></svg>
        +001 555 210 4471
      </li>
      <li>
        <svg viewBox="0 0 12 12"><rect x="3" y="0.5" width="6" height="4"/><rect x="0.5" y="4.5" width="11" height="5" rx="1"/><rect x="3" y="8" width="6" height="3.5"/></svg>
        +001 555 210 3892
      </li>
      <li>
        <svg viewBox="0 0 12 12"><circle cx="6" cy="6" r="5.5"/><path d="M0.5 6h11M6 0.5c-2.5 3-2.5 8 0 11M6 0.5c2.5 3 2.5 8 0 11" stroke="var(--card-dark)" stroke-width="0.9" fill="none"/></svg>
        www.quarrowsignal.com
      </li>
      <li>
        <svg viewBox="0 0 12 12"><rect x="0.5" y="2" width="11" height="8" rx="1"/><path d="M0.8 2.5L6 6.5l5.2-4" stroke="var(--card-dark)" stroke-width="1" fill="none"/></svg>
        info@quarrowsignal.com
      </li>
    </ul>

    <div class="holder">
      <div class="holder-name">Marlene</div>
      <div class="holder-role">Director</div>
    </div>
  </section>

</body>
</html>
```